Brightarc Orthodontics appointment card design

I need appointment cards/ business cards made. Front will be Logo, name, title, email, phone number and location (5263 Walnut Hollow Pkwy, Ste 412, Concord, NC 28027) . the back should have an appointment card (name, time, date) and also 3 addresses listed with a check box so we can check to which location they are going.
Dale Fenwick Orthodontics
- 6735 Orchard Street, Ste 514, Harrisburg, NC 28075
- 3647 Ridgeway Drive NE, Ste 810, Concord, NC 28025
- 2917 Thornbury Corporate Drive, Ste 605, Charlotte, NC 28277
Business card can be horizontal or vertical in Design.
I need to be able to edit it to update and add new employees

Requirements
Must have
• Front:
• - Logo
• - Name & Title (able to be edited)
• - phone (704-555-0186) & Email (need to be able to edit)
• - Address: 5263 Walnut Hollow Pkwy, Ste 412
• Concord, NC 28027
• Back:
• Appointment Card design:
• - Name, time, Date
• - 3 locations w/ a check box so the patient knows where to go:
• Dale Fenwick Orthodontics
• - 6735 Orchard Street, Ste 514, Harrisburg, NC 28075
• - 3647 Ridgeway Drive NE, Ste 810, Concord, NC 28025
• - 2917 Thornbury Corporate Drive, Ste 605, Charlotte, NC 28277

```html
<!DOCTYPE html>
<html lang="en">
<head>
<meta charset="utf-8">
<title>Brightarc Orthodontics – Appointment &amp; Business Card</title>
<link href="https://fonts.googleapis.com/css2?family=Roboto:wght@400;500;700;900&display=swap" rel="stylesheet">
<style>
  :root {
    --blue: #1676c2;
    --blue-dark: #0d5fa3;
    --ink: #4a4a4a;
    --ink-soft: #6b6b6b;
    --line: #3a3a3a;
    --paper: #ffffff;
    --backdrop: #3a3a3c;
  }
  * { box-sizing: border-box; margin: 0; padding: 0; }
  html, body { width: 1200px; height: 1000px; overflow: hidden; }
  body {
    background: var(--backdrop);
    font-family: "Roboto", Arial, sans-serif;
    color: var(--ink);
    position: relative;
  }
  .card {
    position: absolute;
    left: 200px;
    width: 800px;
    height: 420px;
    background: var(--paper);
    border-radius: 26px;
    overflow: hidden;
  }
  /* ---------- Appointment side ---------- */
  .card--appointment { top: 50px; border-bottom: 8px solid var(--blue); }
  .card--appointment .top-band {
    position: absolute; left: 0; top: 0; width: 100%; height: 16px;
    background: var(--blue);
  }
  .appt-title {
    position: absolute; left: 44px; top: 48px;
    font-size: 24px; font-weight: 700; color: var(--blue);
  }
  .field {
    position: absolute; display: flex; align-items: flex-end; gap: 10px;
    font-size: 15px; color: var(--ink-soft);
  }
  .field .rule { flex: 1; border-bottom: 1.5px solid var(--line); height: 1px; }
  .field--name { left: 44px; top: 100px; width: 470px; }
  .field--date { left: 44px; top: 146px; width: 470px; }
  .field--time { left: 44px; top: 192px; width: 712px; }
  .field--time .rule-a { flex: 0 0 350px; }
  .meridiem {
    position: absolute; top: 232px; right: 44px;
    display: flex; gap: 22px; font-size: 16px; color: var(--ink-soft);
  }
  .check { display: inline-flex; align-items: center; gap: 6px; }
  .box {
    width: 16px; height: 16px; border: 2px solid var(--blue); border-radius: 2px;
    display: inline-block;
  }
  .brand-small {
    position: absolute; right: 44px; top: 92px;
    display: flex; align-items: center; gap: 10px;
    font-size: 30px; font-weight: 700; color: var(--blue);
    line-height: 1.05; text-align: right;
  }
  .brand-small .dot { width: 14px; height: 14px; border-radius: 50%; background: var(--blue); }
  .practice {
    position: absolute; left: 0; width: 100%; top: 262px; text-align: center;
    font-size: 16px; color: var(--ink);
  }
  .practice strong { font-size: 22px; font-weight: 700; color: var(--blue); }
  .locations {
    position: absolute; left: 44px; right: 44px; top: 308px;
    display: flex; justify-content: space-between;
  }
  .location {
    width: 220px; text-align: center; font-size: 14px; line-height: 1.35;
    color: var(--ink);
  }
  .location .box { margin-bottom: 8px; }
  /* ---------- Business side ---------- */
  .card--business { top: 530px; }
  .brand-large {
    position: absolute; left: 0; width: 100%; top: 70px;
    display: flex; justify-content: center; align-items: center; gap: 18px;
    font-size: 60px; font-weight: 700; color: var(--blue);
  }
  .brand-large .dot { width: 26px; height: 26px; border-radius: 50%; background: var(--blue); }
  .person {
    position: absolute; left: 0; width: 100%; top: 200px; text-align: center;
  }
  .person-name { font-size: 30px; font-weight: 700; color: var(--blue); letter-spacing: 0.5px; }
  .person-title { font-size: 20px; color: var(--ink); margin-top: 2px; }
  .contact-row {
    position: absolute; left: 0; width: 100%; top: 300px;
    display: flex; justify-content: center; align-items: center; gap: 22px;
  }
  .address { text-align: right; font-size: 19px; line-height: 1.3; color: var(--ink); }
  .divider { width: 2px; height: 62px; background: var(--blue); }
  .contacts { font-size: 19px; line-height: 1.45; color: var(--ink); }
  .contacts li { list-style: none; display: flex; align-items: center; gap: 8px; }
  .contacts svg { width: 16px; height: 16px; fill: var(--blue); }
</style>
</head>
<body>

<section class="card card--appointment" aria-label="Appointment card">
  <div class="top-band"></div>
  <h2 class="appt-title">Next Appointment</h2>

  <div class="field field--name"><span>Name</span><span class="rule"></span></div>
  <div class="field field--date"><span>Date</span><span class="rule"></span></div>
  <div class="field field--time"><span class="rule rule-a"></span><span>Time</span><span class="rule"></span></div>

  <div class="meridiem">
    <span class="check"><span class="box"></span>AM</span>
    <span class="check"><span class="box"></span>PM</span>
  </div>

  <div class="brand-small"><span class="dot"></span><span>Brightarc<br>Orthodontics</span></div>

  <p class="practice"><strong>Dale Fenwick</strong> Orthodontics</p>

  <div class="locations">
    <div class="location"><span class="box"></span><br>6735 Orchard Street, Ste 514,<br>Harrisburg, NC 28075</div>
    <div class="location"><span class="box"></span><br>3647 Ridgeway Drive NE, Ste 810,<br>Concord, NC 28025</div>
    <div class="location"><span class="box"></span><br>2917 Thornbury Corporate Drive,<br>Ste 605, Charlotte, NC 28277</div>
  </div>
</section>

<section class="card card--business" aria-label="Business card">
  <div class="brand-large"><span class="dot"></span><span>Brightarc Orthodontics</span></div>

  <div class="person">
    <p class="person-name">DALE FENWICK</p>
    <p class="person-title">Orthodontics</p>
  </div>

  <div class="contact-row">
    <p class="address">5263 Walnut Hollow Pkwy,<br>Ste 412 - Concord, NC 28027</p>
    <span class="divider"></span>
    <ul class="contacts">
      <li>
        <svg viewBox="0 0 24 24" aria-hidden="true"><path d="M6.6 10.8a15.1 15.1 0 0 0 6.6 6.6l2.2-2.2a1 1 0 0 1 1-.25 11.4 11.4 0 0 0 3.6.57 1 1 0 0 1 1 1V20a1 1 0 0 1-1 1A17 17 0 0 1 3 4a1 1 0 0 1 1-1h3.5a1 1 0 0 1 1 1c0 1.25.2 2.45.57 3.57a1 1 0 0 1-.25 1z"/></svg>
        704-555-0186
      </li>
      <li>
        <svg viewBox="0 0 24 24" aria-hidden="true"><path d="M3 5h18a1 1 0 0 1 1 1v12a1 1 0 0 1-1 1H3a1 1 0 0 1-1-1V6a1 1 0 0 1 1-1zm9 7.2L20 7H4z"/></svg>
        dalefenwick@brightarcmail.com
      </li>
    </ul>
  </div>
</section>

</body>
</html>
```